Plumwick Cat Litter Logo/Package Concept

We need a logo and packaging design concept for a new brand of paper cat littler.

The product is a paper cat litter that utilises special technology to offer superior Odour and moisture absorption - making it more pleasant for customers to clean and have in their home.

It is also Biodegradable and made from Recycled Material so it is friendly to the environment and customers can feel good that they are making an ethical, responsible choice for their cat's litter.

The litter granules are also particularly appealing to cats.

Target Market(s)

Females 25-45 years, cat owners

Industry/Entity Type

Pet Care

Colors
fbed22
9bcb3b
00a990
0492cd
266eb0
6a439a

Requirements
Must have
• - A concept for the Plumwick logo
• - Product title in a large, prominent spot on the front "Paper"
• - Feel; clean, fresh, crisp, simple, inviting, anti-bacterial, sparkling, bright,
• - A close-up picture of the actual litter granules
• - A caricature of a cat OR a photo of a real cat.
• - image imposed on a 3D bag, example supplied. Can use alternative image if preferred.
Nice to have
• The ability for the design to be adapted to expand into crystal/clay littler once we introduce more products into the range.
Should not have
• anything to do with dogs
• feel to natural, holistic, earthy or dull.

```html
<!DOCTYPE html>
<html lang="en">
<head>
<meta charset="utf-8">
<title>Plumwick Paper Cat Litter – Front Panel</title>
<link rel="stylesheet" href="https://fonts.googleapis.com/css2?family=Dosis:wght@700;800&family=PT+Sans+Narrow:wght@400;700&display=swap">
<style>
  :root {
    --stage: #dcdddf;
    --bag-pink: #e35f6d;
    --brand-yellow: #fbd422;
    --white: #ffffff;
    --granule-light: #cfc9b8;
    --granule-dark: #9e9887;
    --fur-light: #f3c27a;
    --fur-mid: #e39a45;
    --fur-dark: #b8672a;
  }
  * { margin: 0; padding: 0; box-sizing: border-box; }
  html, body {
    width: 1111px;
    height: 1200px;
    overflow: hidden;
    background: var(--stage);
  }
  .canvas {
    position: relative;
    width: 1111px;
    height: 1200px;
  }
  .front-panel {
    position: absolute;
    left: 165px;
    top: 40px;
    width: 780px;
    height: 1120px;
    background: var(--bag-pink);
    overflow: hidden;
  }
  .brand-name {
    position: absolute;
    top: 170px;
    left: 0;
    width: 100%;
    text-align: center;
    font-family: "Dosis", sans-serif;
    font-weight: 800;
    font-size: 56px;
    letter-spacing: 1px;
    color: var(--brand-yellow);
  }
  .product-title {
    position: absolute;
    top: 270px;
    left: 0;
    width: 100%;
    text-align: center;
    font-family: "Dosis", sans-serif;
    font-weight: 800;
    color: var(--white);
    line-height: 0.9;
  }
  .product-title .title-main {
    display: block;
    font-size: 176px;
    letter-spacing: 1px;
  }
  .product-title .title-sub {
    display: block;
    font-size: 84px;
    margin-top: 8px;
  }
  .eco-claim {
    position: absolute;
    top: 640px;
    left: 30px;
    width: 240px;
    text-align: right;
    font-family: "PT Sans Narrow", sans-serif;
    color: var(--brand-yellow);
    line-height: 1.1;
    z-index: 3;
  }
  .eco-claim .claim-strong { font-weight: 700; font-size: 34px; display: block; }
  .eco-claim .claim-plain { font-weight: 400; font-size: 28px; display: block; }
  .eco-claim .claim-mid { font-weight: 700; font-size: 28px; display: block; }
  .claim-arrow {
    position: absolute;
    top: 750px;
    left: 200px;
    width: 90px;
    height: 90px;
    z-index: 3;
  }
  .granule-closeup {
    position: absolute;
    top: 610px;
    left: 285px;
    width: 210px;
    height: 320px;
    border-radius: 50%;
    border: 7px solid var(--brand-yellow);
    background: radial-gradient(circle at 45% 40%, var(--granule-light), var(--granule-dark));
    z-index: 2;
  }
  .tech-claims {
    position: absolute;
    top: 640px;
    left: 515px;
    width: 250px;
    font-family: "PT Sans Narrow", sans-serif;
    z-index: 3;
  }
  .tech-label {
    color: var(--white);
    font-weight: 700;
    font-size: 28px;
    margin-bottom: 10px;
  }
  .badge-odour {
    display: inline-block;
    background: var(--brand-yellow);
    color: var(--white);
    font-weight: 700;
    font-size: 40px;
    padding: 4px 14px 6px;
    line-height: 1;
  }
  .badge-moisture {
    display: flex;
    align-items: center;
    gap: 8px;
    width: 190px;
    margin-top: 6px;
    background: var(--white);
    color: var(--bag-pink);
    font-weight: 700;
    font-size: 26px;
    line-height: 0.95;
    padding: 8px 10px;
  }
  .badge-moisture .plus { font-size: 38px; }
  .cat-photo {
    position: absolute;
    left: 150px;
    bottom: 0;
    width: 470px;
    height: 270px;
    border-radius: 46% 46% 0 0 / 36% 36% 0 0;
    background: linear-gradient(180deg, var(--fur-light) 0%, var(--fur-mid) 55%, var(--fur-dark) 100%);
    z-index: 1;
  }
</style>
</head>
<body>
<main class="canvas">
  <section class="front-panel">
    <div class="brand-name">Plumwick</div>

    <h1 class="product-title">
      <span class="title-main">PAPER</span>
      <span class="title-sub">CAT LITTLER</span>
    </h1>

    <p class="eco-claim">
      <span class="claim-strong">Biodegradable</span>
      <span class="claim-plain">and made from</span>
      <span class="claim-mid">Recycled Material</span>
    </p>

    <svg class="claim-arrow" viewBox="0 0 90 90" aria-hidden="true">
      <path d="M12 6 C 0 50, 30 72, 72 72" fill="none" stroke="#fbd422" stroke-width="5" stroke-linecap="round"/>
      <path d="M60 60 L74 72 L60 84" fill="none" stroke="#fbd422" stroke-width="5" stroke-linecap="round" stroke-linejoin="round"/>
    </svg>

    <div class="granule-closeup" role="img" aria-label="Close-up photo of grey paper litter granules"></div>

    <div class="tech-claims">
      <p class="tech-label">Special technology</p>
      <div class="badge-odour">+Odour</div>
      <div class="badge-moisture"><span class="plus">+</span><span>moisture absorption</span></div>
    </div>

    <div class="cat-photo" role="img" aria-label="Photo of a ginger kitten peeking up from the bottom edge"></div>
  </section>
</main>
</body>
</html>
```